Brightwave Exterior cleaning Logo

We need a new business card design, i would like to use our existing logo (attached).
Our logo on the left & a unique graphic design on the right of either a man holding a pressure washer gun & hose with a thumbs up or an image portraying dirt melting off a building or the two incorperated together, or something similar that represents exterior cleaning in progress, an image that shows/explains that we are exterior cleaners/pressure washers. Has to incorporate the zentrix & chatlane symbol perhaps in the bottom corners of the business card.
Existing business symbol on the back of the card with some blank lines for space to hand write quotes or job notes.
Industry/Entity Type
Exterior Cleaning
Contact Information for Business Card
Business mobile No. to be prominent (0472 918 346) Services provided listed as dot points. -Soft Washing -Pressure Washing - Solar Panel Cleaning - All General Exterior Cleaning. Email listed in fineprint (enquiries@tallowbrookwashworks.com.au). Owner Operator - Declan Morrow (this should also be added somewhere prominent). Residential & Comercial Cleaning.
Colors
Designer to choose colors to be used in the design.
Look and feel

```html
<!DOCTYPE html>
<html lang="en">
<head>
<meta charset="utf-8">
<title>Tallowbrook Wash Works – Business Card</title>
<link href="https://fonts.googleapis.com/css2?family=Roboto:wght@400;500;700&display=swap" rel="stylesheet">
<style>
  :root {
    --backdrop: #3b3b3c;
    --card: #141416;
    --edge: #4a5fb0;
    --accent: #4a62b8;
    --ink: #f2f2f2;
    --muted: #bdbdbd;
    --rule: #55565c;
  }
  * { margin: 0; padding: 0; box-sizing: border-box; }
  html, body { width: 1200px; height: 801px; overflow: hidden; }
  body {
    background: var(--backdrop);
    font-family: "Roboto", Arial, sans-serif;
    color: var(--ink);
    display: flex;
    align-items: center;
    justify-content: center;
    gap: 30px;
  }
  .card {
    width: 565px;
    height: 330px;
    background: var(--card);
    border: 1.5px solid var(--edge);
    border-radius: 18px;
    position: relative;
    display: flex;
    align-items: center;
    padding: 0 22px;
  }
  .divider {
    width: 1px;
    height: 160px;
    background: var(--edge);
    flex: none;
  }

  /* Brand lockup */
  .brand {
    width: 150px;
    flex: none;
    display: flex;
    flex-direction: column;
    align-items: flex-start;
    padding-right: 14px;
  }
  .brand-square {
    width: 14px; height: 14px;
    background: var(--accent);
    margin-bottom: 10px;
  }
  .brand-top {
    font-weight: 500;
    font-size: 13px;
    letter-spacing: 0.28em;
    color: var(--ink);
  }
  .brand-bottom {
    font-weight: 700;
    font-size: 17px;
    color: var(--accent);
    margin-top: 3px;
  }

  /* Front */
  .contact { flex: 1; min-width: 0; padding-left: 18px; }
  .owner-name {
    font-weight: 700;
    font-size: 21px;
    color: var(--accent);
    text-transform: uppercase;
  }
  .owner-role { font-size: 12.5px; margin-bottom: 9px; }
  .contact-line {
    display: flex; align-items: center; gap: 6px;
    font-size: 10.5px; line-height: 1.65; white-space: nowrap;
  }
  .contact-line svg { width: 10px; height: 10px; flex: none; }
  .contact-line.phone { font-size: 14px; font-weight: 700; color: var(--accent); }
  .sector { font-size: 11.5px; margin-top: 6px; }

  .cleaning-graphic {
    width: 92px;
    height: 200px;
    flex: none;
    margin-left: 10px;
    border-radius: 8px;
    background: linear-gradient(180deg, #5b6fb8 0%, #2c3560 55%, #1c1e26 100%);
  }

  .social-tag {
    position: absolute;
    bottom: 14px;
    display: flex; align-items: center; gap: 6px;
    font-size: 10.5px; color: var(--muted);
  }
  .social-tag::before {
    content: ""; width: 8px; height: 8px; border-radius: 50%;
    background: var(--accent);
  }
  .social-tag.left { left: 22px; }
  .social-tag.right { right: 22px; }

  /* Back */
  .back .brand-square { background: var(--muted); }
  .back .brand-bottom { color: var(--muted); }
  .back-body { flex: 1; padding-left: 22px; }
  .services { list-style: none; }
  .services li {
    font-size: 14px; line-height: 1.75; text-transform: uppercase;
    display: flex; align-items: center; gap: 10px;
  }
  .services li::before {
    content: ""; width: 6px; height: 6px; border-radius: 50%;
    background: var(--accent);
  }
  .notes { margin-top: 16px; }
  .note-line {
    height: 24px;
    border-bottom: 1px solid var(--rule);
  }
</style>
</head>
<body>

<section class="card front">
  <div class="brand">
    <span class="brand-square"></span>
    <span class="brand-top">TALLOWBROOK</span>
    <span class="brand-bottom">WASH WORKS</span>
  </div>
  <span class="divider"></span>
  <div class="contact">
    <h1 class="owner-name">Declan Morrow</h1>
    <p class="owner-role">Owner Operator</p>
    <p class="contact-line phone">
      <svg viewBox="0 0 10 10"><path d="M2 1l2 2-1 1c.6 1.3 1.7 2.4 3 3l1-1 2 2-1.5 1.5C4 9 1 6 .5 2.5z" fill="currentColor"/></svg>
      0472 918 346
    </p>
    <p class="contact-line">
      <svg viewBox="0 0 10 10"><rect x="0.5" y="2" width="9" height="6.5" fill="#4a62b8"/><path d="M0.5 2l4.5 3.5L9.5 2" stroke="#141416" fill="none"/></svg>
      enquiries@tallowbrookwashworks.com.au
    </p>
    <p class="contact-line">
      <svg viewBox="0 0 10 10"><circle cx="5" cy="5" r="4.3" fill="none" stroke="#4a62b8" stroke-width="1.2"/><path d="M.7 5h8.6M5 .7c-2 2.5-2 6 0 8.6M5 .7c2 2.5 2 6 0 8.6" stroke="#4a62b8" fill="none" stroke-width=".8"/></svg>
      www.tallowbrookwashworks.com.au
    </p>
    <p class="sector">Residential &amp; Comercial Cleaning</p>
  </div>
  <div class="cleaning-graphic" role="img" aria-label="Exterior cleaning in progress: a pressure washer rinsing grime off a building wall"></div>
  <span class="social-tag left">zentrix</span>
  <span class="social-tag right">chatlane</span>
</section>

<section class="card back">
  <div class="brand">
    <span class="brand-square"></span>
    <span class="brand-top">TALLOWBROOK</span>
    <span class="brand-bottom">WASH WORKS</span>
  </div>
  <span class="divider"></span>
  <div class="back-body">
    <ul class="services">
      <li>Soft Washing</li>
      <li>Pressure Washing</li>
      <li>Solar Panel Cleaning</li>
      <li>All General Exterior Cleaning</li>
    </ul>
    <div class="notes" aria-label="Space for quotes and job notes">
      <div class="note-line"></div>
      <div class="note-line"></div>
      <div class="note-line"></div>
    </div>
  </div>
</section>

</body>
</html>
```